Classy, Elegant, Simple Business Card Design

Looking to have a classy, simple, and elegant design. Want a top notch designed business card. I really like the look of the new torvane credit card. I also like the design I attached. I am trying to reach 21-29 year old females for booking us for there wedding or event. We offer Disc Jockey Service, Photo Booth Rentals, and Uplighting .

Target Market(s)

21-28 year old females

Contact Information for Business Card

Has to have logo, website, email, and phone number

Font styles to use
Other font styles liked:
• open to font choice, modern, clean
Designer to choose
33a6d7
0791cd
0555a3
ffffff

Requirements
Must have
• Has to have logo, website, email, and phone number
Nice to have
• I really like the design of the new torvane credit card. I also included my logo and some designs I like
Should not have
• clutter or too much info

```html
<!DOCTYPE html>
<html lang="en">
<head>
<meta charset="UTF-8">
<title>Tidecrest Event Group – Business Card</title>
<link rel="stylesheet" href="https://fonts.googleapis.com/css2?family=Poppins:wght@300;400;500;600&display=swap">
<style>
  :root {
    --sky: #33a6d7;
    --azure: #0791cd;
    --royal: #0555a3;
    --navy: #123f6e;
    --white: #ffffff;
    --muted: #8a8f96;
    --stage: #1e1f22;
  }
  * { margin: 0; padding: 0; box-sizing: border-box; }
  html, body { width: 1200px; height: 885px; overflow: hidden; }
  body {
    background: var(--stage);
    font-family: "Poppins", sans-serif;
    position: relative;
  }
  .card {
    position: absolute;
    width: 560px;
    height: 320px;
    overflow: hidden;
    box-shadow: 0 18px 40px rgba(0,0,0,.45);
  }
  /* front */
  .card-front {
    left: 80px; top: 90px;
    background: radial-gradient(ellipse at 55% 40%, var(--azure) 0%, #1a86c9 55%, #2a7fc4 100%);
    color: var(--white);
  }
  .front-name {
    position: absolute;
    left: 0; right: 0; top: 100px;
    text-align: center;
    font-size: 54px;
    font-weight: 500;
    color: var(--royal);
    letter-spacing: 1px;
  }
  .front-services {
    position: absolute;
    left: 0; right: 0; bottom: 50px;
    text-align: center;
    font-size: 13px;
    font-weight: 400;
    letter-spacing: .3px;
  }
  /* back */
  .card-back {
    left: 560px; top: 470px;
    background: var(--white);
  }
  .back-wave { position: absolute; inset: 0; }
  .brand {
    position: absolute;
    right: 38px; top: 30px;
    text-align: right;
  }
  .brand-name {
    font-size: 34px;
    font-weight: 500;
    color: var(--royal);
    line-height: 1.1;
  }
  .brand-sub {
    font-size: 11px;
    font-weight: 300;
    letter-spacing: 6px;
    color: var(--muted);
    margin-top: 4px;
  }
  .contact {
    position: absolute;
    left: 40px; bottom: 18px;
    color: var(--white);
  }
  .person-name { font-size: 20px; font-weight: 600; line-height: 1.1; }
  .person-role { font-size: 12px; font-weight: 400; margin-bottom: 10px; }
  .contact-list { list-style: none; font-size: 13px; line-height: 1.55; }
  .contact-list li { display: flex; align-items: center; gap: 8px; }
  .contact-list svg { width: 12px; height: 12px; flex: none; }
</style>
</head>
<body>

<section class="card card-front" aria-label="Card front">
  <div class="front-name">Tidecrest</div>
  <p class="front-services">Disc Jockey Service • Photo Booth Rentals • Uplighting</p>
</section>

<section class="card card-back" aria-label="Card back">
  <svg class="back-wave" viewBox="0 0 560 320" preserveAspectRatio="none" aria-hidden="true">
    <path d="M0 146 C 150 96, 300 126, 410 114 S 530 96 560 92 L560 320 L0 320 Z" fill="var(--azure)"/>
    <path d="M0 158 C 150 108, 300 138, 410 126 S 530 108 560 104 L560 320 L0 320 Z" fill="var(--white)"/>
    <path d="M0 166 C 150 116, 300 146, 410 134 S 530 116 560 112 L560 320 L0 320 Z" fill="var(--azure)"/>
    <path d="M0 180 C 150 130, 300 160, 410 148 S 530 130 560 126 L560 320 L0 320 Z" fill="var(--navy)"/>
  </svg>

  <div class="brand">
    <div class="brand-name">Tidecrest</div>
    <div class="brand-sub">EVENT GROUP</div>
  </div>

  <div class="contact">
    <div class="person-name">Daniel Harper</div>
    <div class="person-role">President</div>
    <ul class="contact-list">
      <li>
        <svg viewBox="0 0 24 24" aria-hidden="true"><path fill="#fff" d="M6.6 10.8a15 15 0 0 0 6.6 6.6l2.2-2.2a1 1 0 0 1 1-.25 11.4 11.4 0 0 0 3.6.57 1 1 0 0 1 1 1V20a1 1 0 0 1-1 1A17 17 0 0 1 3 4a1 1 0 0 1 1-1h3.5a1 1 0 0 1 1 1c0 1.25.2 2.45.57 3.57a1 1 0 0 1-.25 1z"/></svg>
        555-014-2278
      </li>
      <li>
        <svg viewBox="0 0 24 24" aria-hidden="true"><rect x="2" y="5" width="20" height="14" rx="1" fill="#fff"/><path d="M2 6l10 7 10-7" stroke="var(--navy)" stroke-width="2" fill="none"/></svg>
        info@tidecrestevents.com
      </li>
      <li>
        <svg viewBox="0 0 24 24" aria-hidden="true"><circle cx="12" cy="12" r="10" fill="#fff"/><path d="M2 12h20M12 2c3 3 3 17 0 20M12 2c-3 3-3 17 0 20" stroke="var(--navy)" stroke-width="1.5" fill="none"/></svg>
        www.tidecrestevents.com
      </li>
    </ul>
  </div>
</section>

</body>
</html>
```